Redesign of business card for Cedar Ridge Mechanical

We are looking for a new design for our business cards for Cedar Ridge Mechanical. We are a plumbing & HVAC construction company, operating on the West Coast of Canada and USA. Logo attached.
Industry/Entity Type
Construction - Plumbing & HVAC
Contact Information for Business Card
Name, address, phone numbers, email, website address
Look and feel
Each slider illustrates characteristics of the customer's brand and the style your logo design should communicate.

```html
<!DOCTYPE html>
<html lang="en">
<head>
<meta charset="utf-8">
<title>Cedar Ridge Mechanical – Business Card</title>
<link href="https://fonts.googleapis.com/css2?family=Poppins:wght@300;400;600&display=swap" rel="stylesheet">
<style>
  :root {
    --backdrop: #232323;
    --card-light: #e2e2e2;
    --card-dark: #141414;
    --ink: #0c0c0c;
    --emboss: #262626;
  }
  * { margin: 0; padding: 0; box-sizing: border-box; }
  html, body { width: 1200px; height: 780px; overflow: hidden; background: var(--backdrop); }
  body { position: relative; font-family: "Poppins", sans-serif; color: var(--ink); }

  .card {
    position: absolute;
    top: 240px;
    width: 520px;
    height: 298px;
    border-radius: 18px;
    overflow: hidden;
  }
  .card--front { left: 50px; background: var(--card-light); }
  .card--back  { left: 630px; background: var(--card-dark); }

  .edge-band { position: absolute; left: 0; bottom: 0; width: 520px; height: 40px; }

  .brand {
    position: absolute;
    left: 30px;
    top: 86px;
    width: 180px;
    display: flex;
    align-items: center;
    gap: 10px;
  }
  .brand__mark { width: 14px; height: 14px; background: var(--ink); flex: none; }
  .brand__name { font-weight: 600; font-size: 17px; line-height: 1.2; color: var(--ink); }

  .divider {
    position: absolute;
    left: 232px;
    top: 52px;
    width: 1.5px;
    height: 176px;
    background: var(--ink);
    transform: rotate(-10deg);
  }

  .contact { position: absolute; left: 262px; top: 44px; width: 240px; }
  .contact__name { font-size: 25px; line-height: 1.1; font-weight: 300; }
  .contact__name strong { font-weight: 600; }
  .contact__title { font-size: 13px; font-weight: 400; margin-bottom: 12px; }
  .contact__address { font-size: 12.5px; line-height: 1.4; margin-bottom: 8px; }
  .contact__list { list-style: none; font-size: 12.5px; line-height: 1.55; }
  .contact__list li { display: flex; align-items: center; gap: 7px; }
  .contact__list svg { width: 11px; height: 11px; flex: none; }

  .back-brand {
    position: absolute;
    inset: 0;
    display: flex;
    align-items: center;
    justify-content: center;
    gap: 14px;
  }
  .back-brand__mark { width: 22px; height: 22px; background: var(--emboss); }
  .back-brand__name { font-weight: 600; font-size: 28px; color: var(--emboss); }
</style>
</head>
<body>

  <section class="card card--front">
    <div class="brand">
      <span class="brand__mark"></span>
      <span class="brand__name">Cedar Ridge Mechanical</span>
    </div>

    <span class="divider"></span>

    <div class="contact">
      <p class="contact__name"><strong>Marta</strong> Kovacs</p>
      <p class="contact__title">Founder &amp; CEO</p>
      <p class="contact__address">1840 Harbor Ln. Suite 310<br>Bellingham, WA 98225</p>
      <ul class="contact__list">
        <li>
          <svg viewBox="0 0 12 12" aria-hidden="true"><path d="M3 1 L5 3.5 L4 5 Q5 7 7 8 L8.5 7 L11 9 L9.5 11 Q4 10.5 1 3 Z" fill="#0c0c0c"/></svg>
          (360) 555-0148
        </li>
        <li>
          <svg viewBox="0 0 12 12" aria-hidden="true"><circle cx="6" cy="6" r="5" fill="none" stroke="#0c0c0c" stroke-width="1.2"/><path d="M1 6 H11 M6 1 Q9 6 6 11 Q3 6 6 1" fill="none" stroke="#0c0c0c" stroke-width="1"/></svg>
          info@yourwebsite.com
        </li>
        <li>
          <svg viewBox="0 0 12 12" aria-hidden="true"><rect x="1" y="2.5" width="10" height="7" fill="none" stroke="#0c0c0c" stroke-width="1.2"/><path d="M1 2.5 L6 7 L11 2.5" fill="none" stroke="#0c0c0c" stroke-width="1.2"/></svg>
          www.yourwebsite.com
        </li>
      </ul>
    </div>

    <svg class="edge-band" viewBox="0 0 520 40" aria-hidden="true">
      <polygon points="0,26 205,26 212,32 212,40 0,40" fill="#0c0c0c"/>
      <polygon points="222,14 520,14 520,40 222,40 222,20" fill="#0c0c0c"/>
    </svg>
  </section>

  <section class="card card--back">
    <div class="back-brand">
      <span class="back-brand__mark"></span>
      <span class="back-brand__name">Cedar Ridge Mechanical</span>
    </div>
  </section>

</body>
</html>
```